Marlith Construction Core Values Wall Design

Core Values Wall Design for our Wall, I’m not exactly sure visually what we would want it to look like. Maybe some acrylic stand offs that could go on brick? If that’s a possibility. That’s where we have the most space in the office. But we could do other locations too.

These are our core values
• Safety
• Integrity
• Quality
• Client-Focused Solutions
• Continuous Improvement
• Positive Culture and Stewardship

Our vision/mission statement is Craft Assured.

```html
<!DOCTYPE html>
<html lang="en">
<head>
<meta charset="utf-8">
<title>Marlith Construction – Core Values Wall Sign</title>
<link href="https://fonts.googleapis.com/css2?family=Poppins:wght@300;400;500;700;800&display=swap" rel="stylesheet">
<style>
  :root {
    --brand-blue: #2c5da8;
    --brand-blue-deep: #1f4f9c;
    --logo-blue: #0d4f94;
    --brand-red: #e8232a;
    --stripe-grey: #c7c8ca;
    --photo-light: #f2f2f2;
    --photo-mid: #d4d4d4;
    --white: #ffffff;
    --tick-cyan: #2aa6e8;
    --wall: #ececec;
  }
  * { box-sizing: border-box; margin: 0; padding: 0; }
  html, body { width: 934px; height: 1200px; overflow: hidden; }
  body {
    background: var(--wall);
    font-family: "Poppins", sans-serif;
    position: relative;
  }
  .sign {
    position: absolute;
    left: 0; top: 289px;
    width: 934px; height: 622px;
    overflow: hidden;
    background: var(--white);
  }
  .sign__art { position: absolute; inset: 0; }

  .brand {
    position: absolute;
    left: 60px; top: 78px;
    color: var(--logo-blue);
    font-weight: 700;
    line-height: 1;
  }
  .brand__name { font-size: 62px; letter-spacing: -1px; display: block; }
  .brand__sub { font-size: 17px; letter-spacing: 9.5px; display: block; margin-top: 8px; }

  .web {
    position: absolute;
    right: 57px; top: 107px;
    color: var(--white);
    font-size: 13px;
    letter-spacing: 1px;
  }
  .title {
    position: absolute;
    right: 58px; top: 150px;
    text-align: right;
    line-height: 0.86;
  }
  .title__core { display: block; color: var(--white); font-weight: 300; font-size: 96px; }
  .title__values { display: block; color: var(--brand-red); font-weight: 800; font-size: 96px; letter-spacing: -2px; }

  .values {
    position: absolute;
    left: 318px; top: 343px;
    display: grid;
    grid-template-columns: 154px auto;
    row-gap: 2px;
    list-style: none;
    color: var(--white);
    font-size: 25px;
    line-height: 36px;
  }
  .values li { display: flex; align-items: center; gap: 9px; }
  .values svg { width: 20px; height: 20px; flex: none; }

  .statement {
    position: absolute;
    left: 60px; top: 505px;
    display: flex; align-items: center; gap: 9px;
    color: var(--white);
    font-size: 28px;
    font-weight: 300;
    white-space: nowrap;
  }
  .statement b { font-weight: 700; }
  .statement__badge {
    background: var(--white);
    color: var(--logo-blue);
    font-size: 17px;
    font-weight: 700;
    padding: 8px 10px;
    line-height: 1.2;
  }
  .statement__rule {
    position: absolute;
    left: 60px; top: 550px;
    width: 500px; height: 2px;
    background: var(--tick-cyan);
    opacity: .8;
  }
</style>
</head>
<body>
  <div class="sign">
    <svg class="sign__art" viewBox="0 0 934 622" aria-hidden="false">
      <defs>
        <linearGradient id="photoTone" x1="0" y1="0" x2="1" y2="1">
          <stop offset="0" stop-color="var(--photo-light)"/>
          <stop offset="1" stop-color="var(--photo-mid)"/>
        </linearGradient>
        <linearGradient id="buildingTone" x1="0" y1="0" x2="1" y2="1">
          <stop offset="0" stop-color="#3468b2"/>
          <stop offset="1" stop-color="var(--brand-blue-deep)"/>
        </linearGradient>
      </defs>
      <rect role="img" aria-label="Greyscale photo of hands reviewing construction plans at a laptop" x="0" y="0" width="934" height="622" fill="url(#photoTone)"/>
      <polygon points="0,248 0,505 172,386" fill="var(--brand-red)"/>
      <polygon points="745,0 760,0 0,520 0,505" fill="var(--stripe-grey)"/>
      <polygon role="img" aria-label="Blue-toned photo of a modern multi-storey building" points="760,0 934,0 934,622 0,622 0,520" fill="url(#buildingTone)"/>
      <polygon points="934,420 934,622 650,622" fill="var(--white)"/>
      <polygon points="934,408 934,414 640,622 631,622" fill="var(--brand-blue-deep)"/>
      <polygon points="934,428 934,433 668,622 660,622" fill="var(--brand-blue-deep)"/>
      <rect role="img" aria-label="Dot grid accent" x="844" y="617" width="0" height="0" fill="none"/>
      <rect role="img" aria-label="Dot grid accent" x="844" y="38" width="52" height="36" fill="var(--white)" opacity=".25"/>
      <rect role="img" aria-label="Dot grid accent" x="38" y="360" width="18" height="50" fill="var(--white)" opacity=".35"/>
      <rect role="img" aria-label="Dot grid accent" x="844" y="573" width="52" height="16" fill="var(--brand-blue-deep)" opacity=".35"/>
      <rect role="img" aria-label="Dotted line accent" x="60" y="573" width="330" height="14" fill="var(--tick-cyan)" opacity=".35"/>
    </svg>

    <div class="brand">
      <span class="brand__name">marlith</span>
      <span class="brand__sub">CONSTRUCTION</span>
    </div>

    <div class="web">www.marlithbuild.com</div>

    <h1 class="title">
      <span class="title__core">CORE</span>
      <span class="title__values">VALUES</span>
    </h1>

    <ul class="values">
      <li><svg viewBox="0 0 20 20"><circle cx="10" cy="10" r="9" fill="#fff"/><path d="M5.5 10.5l3 3 6-7" stroke="var(--tick-cyan)" stroke-width="2.4" fill="none" stroke-linecap="round"/></svg>Safety</li>
      <li><svg viewBox="0 0 20 20"><circle cx="10" cy="10" r="9" fill="#fff"/><path d="M5.5 10.5l3 3 6-7" stroke="var(--tick-cyan)" stroke-width="2.4" fill="none" stroke-linecap="round"/></svg>Client-Focused Solutions</li>
      <li><svg viewBox="0 0 20 20"><circle cx="10" cy="10" r="9" fill="#fff"/><path d="M5.5 10.5l3 3 6-7" stroke="var(--tick-cyan)" stroke-width="2.4" fill="none" stroke-linecap="round"/></svg>Integrity</li>
      <li><svg viewBox="0 0 20 20"><circle cx="10" cy="10" r="9" fill="#fff"/><path d="M5.5 10.5l3 3 6-7" stroke="var(--tick-cyan)" stroke-width="2.4" fill="none" stroke-linecap="round"/></svg>Continuous Improvement</li>
      <li><svg viewBox="0 0 20 20"><circle cx="10" cy="10" r="9" fill="#fff"/><path d="M5.5 10.5l3 3 6-7" stroke="var(--tick-cyan)" stroke-width="2.4" fill="none" stroke-linecap="round"/></svg>Quality</li>
      <li><svg viewBox="0 0 20 20"><circle cx="10" cy="10" r="9" fill="#fff"/><path d="M5.5 10.5l3 3 6-7" stroke="var(--tick-cyan)" stroke-width="2.4" fill="none" stroke-linecap="round"/></svg>Positive Culture &amp; Stewardship</li>
    </ul>

    <p class="statement">
      <span>OUR <b>VISION</b> / <b>MISSION</b> STATEMENT IS</span>
      <span class="statement__badge">CRAFT ASSURED</span>
    </p>
    <div class="statement__rule"></div>
  </div>
</body>
</html>
```